logo & Business Card Design

BrightHaven Termite & Pest Control, I need a great logo, take my ideas and run with them!
I will use this in marketing and website so needs to be eye catching but professional

Target Market(s)

Resedintial & Business

Industry/Entity Type

Marketing

Contact Information for Business Card

Need front side with pertinent info & Logo; back side will have a 25% off initial services Coupon!

Font styles to use
Sans Serif

Colors
ec1f27
1b1b1b

Requirements
Must have
• Professional logo and style
Nice to have
• Raised lettering, black, red, white colors maybe? I'm flexible, but those colors go good on any background, vehicle, uniform, etc...
Should not have
• Cheesy

```html
<!DOCTYPE html>
<html lang="en">
<head>
<meta charset="utf-8">
<title>BrightHaven Termite &amp; Pest Control — Business Card</title>
<link href="https://fonts.googleapis.com/css2?family=Libre+Baskerville:wght@400;700&family=Open+Sans:wght@400;600&display=swap" rel="stylesheet">
<style>
  :root {
    --ink: #0b0b0b;
    --charcoal: #1b1b1b;
    --red: #ec1f27;
    --white: #ffffff;
    --stage: #e6e4e1;
    --muted: #3a3a3a;
  }
  * { box-sizing: border-box; margin: 0; padding: 0; }
  html, body { width: 1200px; height: 915px; overflow: hidden; }
  body {
    background: var(--stage);
    position: relative;
    font-family: "Open Sans", Arial, sans-serif;
  }
  .card {
    position: absolute;
    top: 102px;
    width: 452px;
    height: 710px;
    border-radius: 26px;
    overflow: hidden;
    box-shadow: 0 14px 30px rgba(0,0,0,0.25);
  }
  .card--back { left: 134px; background: var(--ink); }
  .card--front { left: 614px; background: var(--white); }

  .brand-mark {
    position: absolute;
    left: 0; right: 0;
    display: flex;
    align-items: center;
    justify-content: center;
    gap: 12px;
  }
  .brand-mark__square { width: 22px; height: 22px; background: var(--red); }
  .brand-mark__name { font-family: "Open Sans", Arial, sans-serif; font-weight: 600; font-size: 34px; }
  .card--back .brand-mark { top: 300px; }
  .card--back .brand-mark__name { color: var(--white); }
  .card--front .brand-mark { top: 120px; }
  .card--front .brand-mark__name { color: var(--charcoal); font-size: 30px; }

  .tagline {
    position: absolute;
    top: 480px; left: 0; right: 0;
    text-align: center;
    color: var(--white);
    font-family: "Libre Baskerville", Georgia, serif;
    font-size: 19px;
    line-height: 27px;
  }

  .front-panel { position: absolute; inset: 0; width: 452px; height: 710px; }

  .company {
    position: absolute;
    top: 240px; left: 0; right: 0;
    text-align: center;
    font-family: "Libre Baskerville", Georgia, serif;
    font-weight: 700;
    color: var(--charcoal);
  }
  .company__name { font-size: 30px; letter-spacing: 1px; line-height: 40px; }
  .company__trade { font-size: 17px; letter-spacing: 0.5px; line-height: 26px; }

  .person {
    position: absolute;
    top: 385px; left: 0; right: 0;
    text-align: center;
  }
  .person__name { color: var(--red); font-size: 29px; line-height: 38px; }
  .person__title { color: var(--white); font-size: 18px; line-height: 28px; }

  .divider {
    position: absolute;
    top: 478px; left: 44px; right: 44px;
    height: 1px;
    background: linear-gradient(90deg, transparent, var(--muted), transparent);
  }

  .contact {
    position: absolute;
    top: 494px; left: 0; right: 0;
    list-style: none;
    text-align: center;
    color: var(--white);
    font-size: 18px;
    line-height: 37px;
  }
</style>
</head>
<body>
  <section class="card card--back" aria-label="Card back">
    <div class="brand-mark">
      <span class="brand-mark__square"></span>
      <span class="brand-mark__name">BrightHaven</span>
    </div>
    <p class="tagline">“ Trusted Care For Every<br>Property, Big or Small”</p>
  </section>

  <section class="card card--front" aria-label="Card front">
    <svg class="front-panel" viewBox="0 0 452 710" aria-hidden="true">
      <path d="M0 372 C 120 372, 330 360, 452 292 L452 668 L0 668 Z" fill="var(--ink)"/>
    </svg>
    <div class="brand-mark">
      <span class="brand-mark__square"></span>
      <span class="brand-mark__name">BrightHaven</span>
    </div>
    <div class="company">
      <p class="company__name">BRIGHTHAVEN</p>
      <p class="company__trade">TERMITE &amp; PEST CONTROL</p>
    </div>
    <div class="person">
      <p class="person__name">YOUR NAME</p>
      <p class="person__title">Title</p>
    </div>
    <div class="divider"></div>
    <ul class="contact">
      <li>PO Box 418 LAKEVIEW WA&nbsp; 6152</li>
      <li>P: 0412 555 019</li>
      <li>E: info@brighthavenpest.com</li>
      <li>www.brighthavenpest.com</li>
    </ul>
  </section>
</body>
</html>
```